Homemaking training schools needs a Business Card design

Designer, Hello!

No special requirements, good-looking enough.
--------------------------------------------------------------------------

Name: Marcus Dole
Chairman
Tel: 0574-71948263
Mobile: 13857420916
Email: kelvora@mailnest.example
Web: www.prt2019.example
Add: No.258, LanpingJie, BeiyuanQu, Ningbo, Zhejiang

LOGO
Ningbo PRT Homemaking Training School

Target Market(s)

pregnant women, mothers, infants, the elderly and families, including cleaning, cooking, nursing training.

Industry/Entity Type

Business

Contact Information for Business Card

Name: Marcus Dole
Chairman
Tel: 0574-71948263
Mobile: 13857420916
Email: kelvora@mailnest.example
Web: www.prt2019.example

LOGO

Font styles to use
Serif
Sans Serif
Decorative

Requirements
Nice to have
• Feels: clean, specifications, safety, comfort, warmth and happiness.

```html
<!DOCTYPE html>
<html lang="en">
<head>
<meta charset="utf-8">
<title>PingRuiTang Business Card</title>
<link rel="stylesheet" href="https://fonts.googleapis.com/css2?family=Raleway:ital,wght@0,400;0,500;1,400&display=swap">
<style>
  :root {
    --card-dark: #252324;
    --brand-blue: #0a6fc2;
    --brand-pink: #e5067f;
    --text-light: #ffffff;
    --backdrop: #e6e6e4;
  }
  * { margin: 0; padding: 0; box-sizing: border-box; }
  html, body { width: 1200px; height: 900px; overflow: hidden; }
  body {
    background: var(--backdrop);
    font-family: "Raleway", Arial, sans-serif;
    position: relative;
  }
  .card {
    position: absolute;
    left: 280px;
    width: 640px;
    height: 366px;
    overflow: hidden;
    background: var(--card-dark);
    box-shadow: 0 6px 18px rgba(0,0,0,0.18);
  }
  .card-front { top: 62px; }
  .card-back { top: 478px; }
  .card-decor { position: absolute; inset: 0; }

  .brand-name {
    position: absolute;
    text-align: center;
    font-weight: 500;
    color: var(--text-light);
    letter-spacing: 0.5px;
    line-height: 1;
    white-space: nowrap;
  }
  .card-front .brand-name { left: 170px; top: 150px; width: 300px; font-size: 34px; }
  .card-back .brand-name { left: 370px; top: 98px; width: 240px; font-size: 28px; }

  .person { position: absolute; left: 80px; top: 86px; color: var(--text-light); }
  .person-name { font-size: 28px; font-weight: 400; font-style: italic; letter-spacing: 1px; text-transform: uppercase; }
  .person-title { font-size: 22px; font-weight: 400; font-style: italic; margin-top: 2px; }

  .stripe-thin { position: absolute; left: 0; right: 0; top: 202px; height: 5px; background: var(--brand-blue); }
  .contact-band { position: absolute; left: 0; right: 0; top: 214px; bottom: 0; background: var(--brand-blue); }

  .contact-list {
    position: absolute; right: 300px; top: 30px;
    list-style: none; color: var(--text-light);
    font-size: 20px; text-align: right;
  }
  .contact-list li {
    display: flex; align-items: center; justify-content: flex-end;
    gap: 14px; height: 27px; white-space: nowrap;
  }
  .contact-list svg { width: 20px; height: 20px; flex: none; }
  .contact-divider {
    position: absolute; left: 360px; top: 36px; width: 1px; height: 98px;
    background: var(--text-light);
  }
  .address {
    position: absolute; left: 378px; top: 58px;
    color: var(--text-light); font-size: 19px; line-height: 25px; font-style: normal;
  }
</style>
</head>
<body>

<section class="card card-front" aria-label="Card front">
  <svg class="card-decor" viewBox="0 0 640 366" aria-hidden="true">
    <circle cx="-70" cy="200" r="150" fill="var(--brand-blue)"/>
    <circle cx="20" cy="10" r="40" fill="var(--brand-pink)"/>
    <circle cx="-6" cy="200" r="36" fill="var(--brand-pink)"/>
    <circle cx="710" cy="180" r="150" fill="var(--brand-blue)"/>
    <circle cx="622" cy="0" r="40" fill="var(--brand-pink)"/>
    <circle cx="646" cy="180" r="36" fill="var(--brand-pink)"/>
  </svg>
  <p class="brand-name">PingRuiTang</p>
</section>

<section class="card card-back" aria-label="Card back">
  <div class="person">
    <h1 class="person-name">Marcus Dole</h1>
    <p class="person-title">Chairman</p>
  </div>
  <p class="brand-name">PingRuiTang</p>
  <div class="stripe-thin"></div>
  <div class="contact-band">
    <ul class="contact-list">
      <li>0574-71948263
        <svg viewBox="0 0 20 20" fill="none" stroke="#fff" stroke-width="1.5"><circle cx="10" cy="10" r="9"/><path d="M7 5.5l1.6 2.2-1 1.2a6 6 0 0 0 3.5 3.5l1.2-1 2.2 1.6-1 1.6c-3.5.3-8-4.2-7.7-7.7z" fill="#fff" stroke="none"/></svg>
      </li>
      <li>13857420916
        <svg viewBox="0 0 20 20" fill="none" stroke="#fff" stroke-width="1.5"><circle cx="10" cy="10" r="9"/><rect x="7" y="5" width="6" height="10" rx="1"/><path d="M9.2 13h1.6"/></svg>
      </li>
      <li>kelvora@mailnest.example
        <svg viewBox="0 0 20 20" fill="none" stroke="#fff" stroke-width="1.5"><rect x="2" y="4.5" width="16" height="11"/><path d="M2 4.5l8 6 8-6M2 15.5l6-5M18 15.5l-6-5"/></svg>
      </li>
      <li>www.prt2019.example
        <svg viewBox="0 0 20 20" fill="none" stroke="#fff" stroke-width="1.5"><circle cx="10" cy="10" r="9"/><ellipse cx="10" cy="10" rx="4" ry="9"/><path d="M1 10h18M3 5.5h14M3 14.5h14"/></svg>
      </li>
    </ul>
    <div class="contact-divider"></div>
    <address class="address">No.258, LanpingJie<br>BeiyuanQu, Ningbo<br>Zhejiang</address>
  </div>
</section>

</body>
</html>
```